Design 4 pages for an event discovery website

This is a contest for the design of 4 pages for an events discovery website. The feature is part of the new sign-up process.

Please see the attached document for a full scope, mockups and the parent category icons.

Target Market(s)

18-35 Australian event goers

Industry/Entity Type

Events

Number of Pages Required

4 page

```html
<!DOCTYPE html>
<html lang="en">
<head>
<meta charset="utf-8">
<title>Venuly – Sign Up</title>
<link rel="stylesheet" href="https://fonts.googleapis.com/css2?family=Open+Sans:wght@400;600&display=swap">
<style>
  :root {
    --ink: #ffffff;
    --ink-dark: #1a1a1a;
    --rust: #b63f10;
    --rust-login: #b8400f;
    --social-blue: #2633b5;
    --social-divider: #1d27a0;
    --header-veil: rgba(60, 35, 20, 0.55);
    --field: rgba(220, 190, 150, 0.45);
    --field-button: #3a2a1e;
    --signup-button: rgba(150, 140, 125, 0.75);
    --panel: rgba(40, 25, 20, 0.45);
  }
  * { box-sizing: border-box; margin: 0; padding: 0; }
  html, body { width: 1200px; height: 831px; overflow: hidden; }
  body {
    position: relative;
    font-family: "Open Sans", sans-serif;
    color: var(--ink);
    background: #2a1a14;
  }
  .hero-backdrop {
    position: absolute; inset: 0 0 85px 0;
    background:
      radial-gradient(ellipse 320px 200px at 180px 30px, rgba(240,170,60,0.85), transparent 70%),
      radial-gradient(ellipse 260px 180px at 470px 90px, rgba(220,120,110,0.7), transparent 70%),
      radial-gradient(ellipse 300px 220px at 820px 60px, rgba(220,130,60,0.6), transparent 70%),
      radial-gradient(ellipse 160px 200px at 1000px 470px, rgba(220,220,80,0.55), transparent 70%),
      radial-gradient(ellipse 200px 160px at 60px 460px, rgba(60,90,150,0.5), transparent 70%),
      linear-gradient(180deg, #8a5230 0%, #6b3e2a 35%, #3e2a22 65%, #1f1410 100%);
  }
  .site-header {
    position: absolute; left: 0; top: 0; width: 1200px; height: 90px;
    background: var(--header-veil);
  }
  .brand {
    position: absolute; left: 60px; top: 24px;
    font-size: 36px; font-weight: 600; line-height: 44px;
  }
  .nav-link {
    position: absolute; left: 218px; top: 37px;
    font-size: 14px; font-weight: 600;
  }
  .search {
    position: absolute; left: 558px; top: 30px; width: 287px; height: 32px;
    background: var(--field);
  }
  .search-button {
    position: absolute; right: 0; top: 0; width: 29px; height: 32px;
    background: var(--field-button);
    display: flex; align-items: center; justify-content: center;
  }
  .header-button {
    position: absolute; top: 30px; width: 132px; height: 32px;
    font-size: 14.5px; font-weight: 600; letter-spacing: 0.3px;
    display: flex; align-items: center; justify-content: center;
  }
  .header-button--signup { left: 861px; background: var(--signup-button); color: var(--ink-dark); }
  .header-button--login { left: 1001px; background: var(--rust-login); }

  .section-title { position: absolute; font-size: 35px; font-weight: 400; line-height: 44px; }
  .signup-title { left: 74px; top: 258px; }
  .benefits-title { left: 555px; top: 253px; }

  .social-connect {
    position: absolute; left: 75px; top: 330px; width: 379px; height: 184px;
    background: var(--social-blue);
  }
  .social-connect__mark {
    position: absolute; left: 40px; top: 72px; width: 40px; height: 40px;
    border-radius: 50%; background: var(--ink);
  }
  .social-connect__divider {
    position: absolute; left: 115px; top: 18px; width: 1px; height: 148px;
    background: var(--social-divider);
  }
  .social-connect__label {
    position: absolute; left: 157px; top: 24px;
    font-size: 33px; line-height: 44px;
  }
  .alt-signup {
    position: absolute; left: 74px; top: 538px; font-size: 19.5px;
  }
  .alt-signup a { color: var(--ink); text-decoration: underline; }

  .benefits-panel {
    position: absolute; left: 537px; top: 330px; width: 602px; height: 228px;
    background: var(--panel);
  }
  .benefits-list { list-style: none; position: absolute; left: 24px; top: 12px; }
  .benefits-list li {
    position: relative; padding-left: 24px;
    font-size: 15.5px; line-height: 35.4px; white-space: nowrap;
  }
  .benefits-list svg { position: absolute; left: 0; top: 13px; }

  .carousel-dots { position: absolute; left: 560px; top: 717px; display: flex; gap: 13px; }
  .carousel-dots span {
    width: 10px; height: 10px; border-radius: 50%; border: 1.5px solid var(--ink);
  }
  .carousel-dots span.is-active { background: var(--ink); }

  .site-footer {
    position: absolute; left: 0; top: 746px; width: 1200px; height: 85px;
    background: var(--rust);
  }
  .footer-links { position: absolute; left: 60px; top: 29px; font-size: 17px; }
  .footer-links a { color: var(--ink); text-decoration: none; }
  .footer-links a.is-underlined { text-decoration: underline; }
  .footer-social {
    position: absolute; right: 64px; top: 32px; display: flex; gap: 12px;
    font-size: 13px; font-weight: 600;
  }
</style>
</head>
<body>
  <div class="hero-backdrop" role="img" aria-label="Blurred photo of a concert crowd with raised hands in front of a lit stage"></div>

  <header class="site-header">
    <div class="brand">Venuly</div>
    <div class="nav-link">Find Events</div>
    <div class="search">
      <div class="search-button">
        <svg width="12" height="12" viewBox="0 0 12 12" aria-hidden="true">
          <circle cx="5" cy="5" r="3.8" fill="none" stroke="#fff" stroke-width="1.5"/>
          <line x1="7.8" y1="7.8" x2="11" y2="11" stroke="#fff" stroke-width="1.6"/>
        </svg>
      </div>
    </div>
    <div class="header-button header-button--signup">SIGNUP</div>
    <div class="header-button header-button--login">LOGIN</div>
  </header>

  <h1 class="section-title signup-title">Sign Up</h1>
  <div class="social-connect">
    <div class="social-connect__mark"></div>
    <div class="social-connect__divider"></div>
    <div class="social-connect__label">Connect<br>With<br>Friendbase</div>
  </div>
  <p class="alt-signup">Or <a href="#">Click here</a> to sign up without Friendbase</p>

  <h2 class="section-title benefits-title">Benefits</h2>
  <div class="benefits-panel">
    <ul class="benefits-list">
      <li><svg width="13" height="11" viewBox="0 0 13 11"><path d="M1 6 L4.5 10 L12 1" fill="none" stroke="#fff" stroke-width="1.2"/></svg>Get personalised event recommendations</li>
      <li><svg width="13" height="11" viewBox="0 0 13 11"><path d="M1 6 L4.5 10 L12 1" fill="none" stroke="#fff" stroke-width="1.2"/></svg>Get notified about your favourite events - never miss out again</li>
      <li><svg width="13" height="11" viewBox="0 0 13 11"><path d="M1 6 L4.5 10 L12 1" fill="none" stroke="#fff" stroke-width="1.2"/></svg>Follow all your favourite artists, musicians, teams and players in one place</li>
      <li><svg width="13" height="11" viewBox="0 0 13 11"><path d="M1 6 L4.5 10 L12 1" fill="none" stroke="#fff" stroke-width="1.2"/></svg>Follow your favourite local venues to know everything happening there</li>
      <li><svg width="13" height="11" viewBox="0 0 13 11"><path d="M1 6 L4.5 10 L12 1" fill="none" stroke="#fff" stroke-width="1.2"/></svg>Get curated news and feature content on your favourite artists (coming soon)</li>
      <li><svg width="13" height="11" viewBox="0 0 13 11"><path d="M1 6 L4.5 10 L12 1" fill="none" stroke="#fff" stroke-width="1.2"/></svg>Invite your mates to events via Friendbase (Friendbase sign-up only)</li>
    </ul>
  </div>

  <div class="carousel-dots"><span class="is-active"></span><span></span><span></span><span></span></div>

  <footer class="site-footer">
    <p class="footer-links">©2015 yoursite - <a href="#">Terms of Service</a> - <a href="#">Privacy</a> - <a href="#" class="is-underlined">Contact</a></p>
    <div class="footer-social"><span>Friendbase</span><span>Chirpa</span><span>Plusly</span></div>
  </footer>
</body>
</html>
```